Dunmore Roofing

Want a professional looking business card

Industry/Entity Type

Business

Contact Information for Business Card

Paul Dunmore ( Owner) paul@dunmoreroofing-example.com, www.dunmoreroofing-example.com, Adress: 4172 Township road 43 Plantagenet,ON K9X4T2

```html
<!DOCTYPE html>
<html lang="en">
<head>
<meta charset="utf-8">
<title>Dunmore Roofing – Business Card</title>
<link href="https://fonts.googleapis.com/css2?family=Roboto:wght@400;700;900&family=Roboto+Condensed:wght@400;500&display=swap" rel="stylesheet">
<style>
  :root {
    --backdrop: #2a2a2a;
    --card-white: #f1f1f1;
    --brand-blue: #163f80;
    --roof-grey: #737373;
    --text-light: #ffffff;
  }
  html, body {
    margin: 0;
    padding: 0;
    width: 1200px;
    height: 777px;
    overflow: hidden;
    background: var(--backdrop);
  }
  .stage {
    position: absolute;
    left: 0;
    top: 0;
    width: 1482px;
    height: 960px;
    transform: scale(0.8097);
    transform-origin: 0 0;
  }
  .card {
    position: absolute;
    top: 309px;
    width: 600px;
    height: 343px;
    background: var(--card-white);
    overflow: hidden;
    box-shadow: 0 2px 6px rgba(0,0,0,0.45);
  }
  .card--front { left: 132px; }
  .card--back  { left: 750px; }
  .card__art {
    position: absolute;
    inset: 0;
    width: 600px;
    height: 343px;
  }
  .brand-name {
    position: absolute;
    left: 60px;
    top: 170px;
    width: 240px;
    text-align: center;
    font-family: 'Roboto', sans-serif;
    font-weight: 900;
    color: var(--brand-blue);
    line-height: 1;
  }
  .brand-name__main {
    display: block;
    font-size: 36px;
    letter-spacing: 3px;
    margin-right: -3px;
  }
  .brand-name__sub {
    display: block;
    font-size: 14px;
    letter-spacing: 26px;
    margin-top: 6px;
    margin-right: -26px;
  }
  .contact {
    position: absolute;
    right: 45px;
    top: 90px;
    text-align: right;
    color: var(--text-light);
    font-family: 'Roboto', sans-serif;
    font-size: 15px;
    line-height: 18px;
  }
  .contact__name {
    font-family: 'Roboto Condensed', sans-serif;
    font-weight: 500;
    font-size: 25px;
    line-height: 28px;
  }
  .contact__role {
    font-family: 'Roboto Condensed', sans-serif;
    font-weight: 400;
    font-size: 17px;
    line-height: 20px;
    margin-bottom: 8px;
  }
  .contact__address { margin-bottom: 9px; }
  .contact__line {
    display: flex;
    justify-content: flex-end;
    align-items: center;
    gap: 7px;
    height: 19px;
  }
  .contact__icon {
    width: 13px;
    height: 13px;
    flex: none;
  }
</style>
</head>
<body>
<div class="stage">
  <section class="card card--front">
    <svg class="card__art" viewBox="0 0 600 343" aria-hidden="true">
      <polygon points="594,0 600,0 600,8" fill="var(--brand-blue)"/>
      <polygon points="537,22 571,58 337,343 274,343" fill="var(--roof-grey)"/>
      <rect x="546" y="205" width="44" height="44" fill="var(--roof-grey)"/>
      <rect x="546" y="265" width="44" height="44" fill="var(--roof-grey)"/>
    </svg>
    <div class="brand-name">
      <span class="brand-name__main">DUNMORE</span>
      <span class="brand-name__sub">ROOFING</span>
    </div>
  </section>

  <section class="card card--back">
    <svg class="card__art" viewBox="0 0 600 343" aria-hidden="true">
      <polygon points="0,0 600,0 600,343 305,343" fill="var(--brand-blue)"/>
      <rect x="16" y="205" width="44" height="44" fill="var(--roof-grey)"/>
      <rect x="16" y="265" width="44" height="44" fill="var(--roof-grey)"/>
    </svg>
    <div class="contact">
      <div class="contact__name">PAUL DUNMORE</div>
      <div class="contact__role">OWNER</div>
      <div class="contact__address">4172 Township road 43<br>Alderbrook, QX K9X4T2</div>
      <div class="contact__line">613 555 0148
        <svg class="contact__icon" viewBox="0 0 24 24"><path fill="#fff" d="M6.6 10.8a15.1 15.1 0 0 0 6.6 6.6l2.2-2.2c.3-.3.7-.4 1-.2 1.1.4 2.3.6 3.6.6.6 0 1 .4 1 1V20c0 .6-.4 1-1 1A17 17 0 0 1 3 4c0-.6.4-1 1-1h3.5c.6 0 1 .4 1 1 0 1.3.2 2.5.6 3.6.1.3 0 .7-.2 1z"/></svg>
      </div>
      <div class="contact__line">paul@dunmoreroofing-example.com
        <svg class="contact__icon" viewBox="0 0 24 24"><rect x="2" y="5" width="20" height="14" fill="#fff"/><path d="M2 5l10 8 10-8" fill="none" stroke="var(--brand-blue)" stroke-width="2"/></svg>
      </div>
      <div class="contact__line">www.dunmoreroofing-example.com
        <svg class="contact__icon" viewBox="0 0 24 24"><circle cx="12" cy="12" r="11" fill="#fff"/><path d="M1 12h22M12 1c-4 4-4 18 0 22M12 1c4 4 4 18 0 22" fill="none" stroke="var(--brand-blue)" stroke-width="1.6"/></svg>
      </div>
    </div>
  </section>
</div>
</body>
</html>
```